Road Construction Company needs business cards

We would like a new business card designed for our business.

We're a road construction company based in Qld, Australia.

Can the business card please have the following information on it.

Name: Warren Halbeck
Position: General Manager
Phone: 0472 915 348
Email: Warren.halbeck@tovrin.com.au
Address: 87 Marrow Ave, Pendlebay, QLD, 4023
Website: www.tovrin.com.au

Visually we'd like the card to be professional and simple.

Attached is our logo.

Our website is www.tovrin.com.au

Target Market(s)

Men aged 25-60

Contact Information for Business Card

As listed in project description

Font styles to use
Serif

Requirements
Must have
• Large logo on back of card

```html
<!DOCTYPE html>
<html lang="en">
<head>
<meta charset="utf-8">
<title>Tovrin Road Construction – Business Card</title>
<link href="https://fonts.googleapis.com/css2?family=Inter:wght@400;700;800&display=swap" rel="stylesheet">
<style>
  :root {
    --backdrop: #9a9a9a;
    --brand-blue: #0b53a4;
    --brand-blue-deep: #0a3f86;
    --accent-blue: #2ea3d8;
    --paper: #ffffff;
    --ink: #3d3d3d;
  }
  * { margin: 0; padding: 0; box-sizing: border-box; }
  html, body {
    width: 1200px; height: 588px; overflow: hidden;
    background: var(--backdrop);
    font-family: "Inter", Arial, sans-serif;
  }
  .canvas { position: relative; width: 1200px; height: 588px; }
  .card {
    position: absolute; top: 150px;
    width: 486px; height: 288px; overflow: hidden;
  }
  .card-front {
    left: 87px;
    background: linear-gradient(135deg, var(--brand-blue-deep) 0%, var(--brand-blue) 45%, #1762b4 70%, var(--brand-blue) 100%);
    display: flex; align-items: center; justify-content: center;
  }
  .front-wordmark {
    color: var(--paper);
    font-weight: 800; font-size: 56px; letter-spacing: 1px;
    margin-bottom: 6px;
  }
  .card-back { left: 627px; background: var(--paper); }
  .back-wordmark {
    position: absolute; left: 28px; top: 124px; width: 205px;
    color: var(--brand-blue);
    font-weight: 800; font-size: 40px; letter-spacing: 1px; text-align: center;
  }
  .divider {
    position: absolute; left: 246px; top: 79px;
    width: 1.5px; height: 126px; background: var(--brand-blue);
  }
  .contact { position: absolute; left: 258px; top: 76px; color: var(--ink); }
  .contact-name {
    color: var(--brand-blue); font-weight: 700; font-size: 18.5px;
    line-height: 22px; text-transform: uppercase; letter-spacing: 0.1px;
  }
  .contact-role { font-size: 13.5px; line-height: 18px; margin-top: 1px; }
  .contact-address { font-size: 13.5px; line-height: 18px; margin-top: 9px; }
  .contact-lines { margin-top: 12px; font-size: 13.5px; line-height: 18px; }
  .contact-line { display: flex; align-items: center; gap: 4px; }
  .contact-line svg { width: 11px; height: 11px; flex: none; }
  .strip-accent {
    position: absolute; left: 0; bottom: 0;
    width: 320px; height: 10px; background: var(--accent-blue);
  }
  .strip-web {
    position: absolute; right: 0; bottom: 0;
    width: 186px; height: 29px; background: var(--brand-blue);
    clip-path: polygon(20px 0, 100% 0, 100% 100%, 0 100%);
    color: var(--paper); font-size: 13px;
    display: flex; align-items: center; padding-left: 34px;
  }
</style>
</head>
<body>
<main class="canvas">
  <section class="card card-front" aria-label="Card front">
    <div class="front-wordmark">TOVRIN</div>
  </section>

  <section class="card card-back" aria-label="Card back">
    <div class="back-wordmark">TOVRIN</div>
    <div class="divider"></div>
    <div class="contact">
      <div class="contact-name">Warren Halbeck</div>
      <div class="contact-role">General Manager</div>
      <div class="contact-address">87 Marrow Ave<br>Pendlebay, QLD, 4023</div>
      <div class="contact-lines">
        <div class="contact-line">
          <svg viewBox="0 0 24 24" aria-hidden="true"><path fill="#2ea3d8" d="M6.6 10.8a15.1 15.1 0 0 0 6.6 6.6l2.2-2.2c.3-.3.7-.4 1-.2 1.1.4 2.3.6 3.6.6.6 0 1 .4 1 1V20c0 .6-.4 1-1 1C10.6 21 3 13.4 3 4c0-.6.4-1 1-1h3.5c.6 0 1 .4 1 1 0 1.3.2 2.5.6 3.6.1.3 0 .7-.2 1z"/></svg>
          <span>0472 915 348</span>
        </div>
        <div class="contact-line">
          <svg viewBox="0 0 24 24" aria-hidden="true"><path fill="#2ea3d8" d="M2 5h20v14H2z M2 5l10 7 10-7" /><path fill="none" stroke="#fff" stroke-width="1.6" d="M2.5 6l9.5 6.5L21.5 6"/></svg>
          <span>Warren.halbeck@tovrin.com.au</span>
        </div>
      </div>
    </div>
    <div class="strip-accent"></div>
    <div class="strip-web">www.tovrin.com.au</div>
  </section>
</main>
</body>
</html>
```